Business Card Design

New business card design

Target Market(s)

Residential & Commercial Property Managers

Industry/Entity Type

Plumbing Services

Contact Information for Business Card

Name - Rowan Keddle, title - Director, Phone Number - 0431 286 517, email - rowan@tbk-plumbing.com.au, Company ABN - 73 215 904 386,

Font styles to use
Sans Serif

Colors
0054AA
0677BA
7BADD7
CADEEF
E8F1F8

```html
<!DOCTYPE html>
<html lang="en">
<head>
<meta charset="utf-8">
<title>TBK Plumbing Services – Business Cards</title>
<link href="https://fonts.googleapis.com/css2?family=Montserrat:wght@300;400;500;700&display=swap" rel="stylesheet">
<style>
  :root{
    --page:#0c0c0c;
    --card:#151515;
    --card-curve:#1a1a1a;
    --card-curve-deep:#1e1e1e;
    --logo:#2c3a46;
    --accent:#00aeef;
    --muted:#6e655c;
    --divider:#4d463f;
  }
  *{box-sizing:border-box;margin:0;padding:0}
  html,body{width:1200px;height:1200px;overflow:hidden;background:var(--page)}
  body{font-family:"Montserrat",sans-serif;position:relative}

  .card{
    position:absolute;left:220px;width:760px;height:434px;
    background:var(--card);border-radius:22px;overflow:hidden;
    box-shadow:0 18px 40px rgba(0,0,0,.6);
  }
  .card--front{top:110px}
  .card--back{top:650px;border-bottom:9px solid var(--accent)}

  .card__curves{position:absolute;inset:0;width:100%;height:100%}

  .brand{position:absolute;display:flex;align-items:center;gap:12px}
  .brand__dot{width:20px;height:20px;border-radius:50%;background:var(--accent);flex:none}
  .brand__name{font-weight:500;color:var(--logo);letter-spacing:.04em;white-space:nowrap}
  .card--front .brand{left:0;right:0;top:190px;justify-content:center}
  .card--front .brand__name{font-size:44px}
  .card--back .brand{left:40px;top:200px}
  .card--back .brand__name{font-size:24px}
  .card--back .brand__dot{width:16px;height:16px}

  .divider{position:absolute;left:400px;top:120px;width:1px;height:190px;background:var(--divider)}

  .contact{position:absolute;left:426px;top:130px;color:var(--muted)}
  .contact__name{font-weight:700;font-size:24px;color:var(--accent);letter-spacing:.01em;text-transform:uppercase}
  .contact__title{font-size:17px;font-weight:400;margin-bottom:14px}
  .contact__line{display:flex;align-items:center;gap:10px;font-size:17px;font-weight:500;margin-bottom:8px;white-space:nowrap}
  .contact__icon{width:16px;height:16px;flex:none}
  .contact__line--plain{padding-left:26px}
</style>
</head>
<body>

<section class="card card--front" aria-label="Card front">
  <svg class="card__curves" viewBox="0 0 760 434" aria-hidden="true">
    <path d="M0 0 H110 C330 60 390 250 300 434 H0 Z" fill="var(--card-curve-deep)"/>
    <path d="M0 0 H80 C290 70 340 250 250 434 H0 Z" fill="var(--card-curve)"/>
  </svg>
  <div class="brand">
    <span class="brand__name">TBK Plumbing Services</span>
    <span class="brand__dot"></span>
  </div>
</section>

<section class="card card--back" aria-label="Card back">
  <div class="brand">
    <span class="brand__name">TBK Plumbing Services</span>
    <span class="brand__dot"></span>
  </div>
  <div class="divider"></div>
  <div class="contact">
    <p class="contact__name">Rowan Keddle</p>
    <p class="contact__title">Director</p>
    <p class="contact__line">
      <svg class="contact__icon" viewBox="0 0 16 16" aria-hidden="true"><path d="M3 1.5h3l1.2 3.2-1.8 1.3a9 9 0 0 0 4.6 4.6l1.3-1.8 3.2 1.2v3a1.5 1.5 0 0 1-1.6 1.5A13 13 0 0 1 1.5 3.1 1.5 1.5 0 0 1 3 1.5z" fill="var(--accent)"/></svg>
      0431 286 517
    </p>
    <p class="contact__line">
      <svg class="contact__icon" viewBox="0 0 16 16" aria-hidden="true"><rect x="1" y="3" width="14" height="10" rx="1" fill="none" stroke="var(--accent)" stroke-width="1.6"/><path d="M1.5 3.5 8 9 14.5 3.5" fill="none" stroke="var(--accent)" stroke-width="1.6"/></svg>
      rowan@tbk-plumbing.com.au
    </p>
    <p class="contact__line contact__line--plain">ABN: 73 215 904 386</p>
  </div>
</section>

</body>
</html>
```